Baseball Coaching Camp for 5-14year olds needs sales campaign

Local baseball coaching camp for children is in it's 22nd year running a 4-5 week series of summer camps. Each year we use email marketing beginning around December to sell our camps to the parents to sign up their children for one or more weeks. All information about the camps can be seen on our website at https://hemmingtarn.com/. In the past we have had success by changing the look of the emails each month and offering a decreasing discount as the camps get closer.

Our target market is the parents of children ages 5-14years old who like and play baseball and are interested in improving their skills in a fun environment during the Summer months.

We would like to improve the sales by developing new creative and imaginative emails for this season. We need 6 to 8 quality ads that can somehow relate to each other , these ads will be sent via our mailing list as well as used on social media. One of the owners thought it would be nice to use the "river of lanterns" theme though we are open to all ideas.
We have given you access to a dropbox link with examples of past campaigns along with artwork and images here
https://www.filequay.net/sh/q7ptr2mzk4wnhd/BBReo-kmTulf5pLXU318jw6Hb?dl=0

```html
<!DOCTYPE html>
<html lang="en">
<head>
<meta charset="utf-8">
<title>Hemmingtarn Baseball Academy</title>
<link rel="stylesheet" href="https://fonts.googleapis.com/css2?family=Montserrat:wght@600;700;800&family=Roboto:wght@300;400;500&display=swap">
<style>
  :root {
    --navy: #252a36;
    --blue: #3b4aa0;
    --blue-soft: #4454ab;
    --brand: #34429c;
    --text: #555861;
    --text-dark: #33363d;
    --white: #ffffff;
    --line: #5a6070;
  }
  * { box-sizing: border-box; margin: 0; padding: 0; }
  html, body { width: 1200px; height: 3050px; overflow: hidden; background: var(--white); }
  body { font-family: "Roboto", Arial, sans-serif; color: var(--text); position: relative; }

  .top-rule { position: absolute; left: 0; top: 0; width: 1200px; height: 6px; background: var(--blue); }

  .site-header { position: absolute; left: 0; top: 6px; width: 1200px; height: 127px; }
  .brand-name {
    position: absolute; left: 150px; top: 38px;
    font-family: "Montserrat", sans-serif; font-weight: 800; font-size: 40px;
    color: var(--brand); letter-spacing: 1px;
  }
  .call { position: absolute; left: 686px; top: 30px; display: flex; align-items: center; }
  .call svg { width: 70px; height: 70px; margin-right: 36px; }
  .call-label { font-size: 25px; font-weight: 500; color: var(--text-dark); line-height: 32px; }
  .call-number { font-size: 36px; font-weight: 500; color: var(--blue); line-height: 42px; }

  .hero-photo {
    position: absolute; left: 0; top: 133px; width: 1200px; height: 600px;
    background: linear-gradient(135deg, #3f5a2a 0%, #6b7f3a 35%, #d9a92a 60%, #e9b933 80%, #8a9a5a 100%);
  }
  .title-frame {
    position: absolute; left: 150px; top: 655px; width: 900px; height: 140px;
    background: var(--white); padding: 12px 12px 0;
  }
  .title-box {
    width: 100%; height: 100%; background: var(--navy);
    display: flex; align-items: center; justify-content: center; text-align: center;
  }
  .title-box h1 {
    font-family: "Montserrat", sans-serif; font-weight: 700; font-size: 41px;
    line-height: 52px; color: var(--white); letter-spacing: 0.5px;
  }

  .intro {
    position: absolute; left: 130px; top: 860px; width: 940px;
    text-align: center; font-size: 22.5px; font-weight: 300; line-height: 37.5px; color: var(--text);
  }

  .about { position: absolute; left: 0; top: 1086px; width: 1200px; height: 525px; }
  .about-photo {
    position: absolute; inset: 0;
    background: linear-gradient(90deg, #2e2f33 0%, #55565a 30%, #d7b237 55%, #e6bd3c 75%, #3a3b40 100%);
  }
  .about-card {
    position: absolute; left: 150px; top: 71px; width: 450px; height: 383px;
    background: rgba(255,255,255,0.88); text-align: center; padding: 40px 14px 0;
  }
  .about-card h2 {
    font-family: "Montserrat", sans-serif; font-weight: 700; font-size: 39px;
    color: var(--navy); margin-bottom: 20px;
  }
  .about-card p { font-size: 16.5px; line-height: 33px; color: var(--text-dark); }
  .about-card a { color: var(--blue); text-decoration: none; }

  .academy {
    position: absolute; left: 0; top: 1611px; width: 1200px; height: 495px;
    background: linear-gradient(180deg, var(--blue-soft), var(--blue));
  }
  .academy h2 {
    position: absolute; left: 0; top: 64px; width: 1200px; text-align: center;
    font-family: "Montserrat", sans-serif; font-weight: 700; font-size: 38px; color: var(--white);
  }
  .week {
    position: absolute; width: 438px; height: 120px; background: var(--white);
    border-radius: 60px; display: flex; align-items: center; padding-left: 9px;
    box-shadow: 0 6px 14px rgba(0,0,0,0.18);
  }
  .week .price {
    width: 102px; height: 102px; border-radius: 50%; background: var(--navy);
    color: var(--white); font-size: 28px; font-weight: 500; flex: none;
    display: flex; align-items: center; justify-content: center;
  }
  .week .details { margin-left: 15px; font-size: 22px; line-height: 31px; color: var(--text); }
  .week .label { color: var(--blue); font-weight: 500; }
  .w1 { left: 150px; top: 159px; }
  .w2 { left: 612px; top: 159px; }
  .w3 { left: 150px; top: 301px; }
  .w4 { left: 612px; top: 301px; }

  .objectives-photo {
    position: absolute; left: 525px; top: 2229px; width: 600px; height: 449px;
    background: linear-gradient(180deg, #7aa6d8 0%, #4c7a3a 45%, #d4ad2f 72%, #6f9a45 100%);
  }
  .objectives-card {
    position: absolute; left: 75px; top: 2259px; width: 543px; height: 389px;
    background: var(--white); padding: 44px 43px 0;
    box-shadow: 0 4px 18px rgba(0,0,0,0.16);
  }
  .objectives-card h2 {
    font-family: "Montserrat", sans-serif; font-weight: 600; font-size: 36px;
    color: var(--navy); margin-bottom: 24px;
  }
  .objectives-card p { font-size: 16.5px; line-height: 31.5px; text-align: justify; color: var(--text); }

  .site-footer { position: absolute; left: 0; top: 2800px; width: 1200px; height: 250px; background: var(--navy); }
  .footer-brand {
    position: absolute; left: 150px; top: 65px;
    font-family: "Montserrat", sans-serif; font-weight: 800; font-size: 40px;
    color: #5262bd; letter-spacing: 1px;
  }
  .contact { position: absolute; right: 147px; color: var(--white); font-size: 22px; font-weight: 500; display: flex; align-items: center; }
  .contact svg { width: 20px; height: 20px; margin-right: 14px; fill: var(--white); }
  .contact .sep { margin: 0 22px; }
  .contact-1 { top: 59px; }
  .contact-2 { top: 102px; font-size: 21px; }
  .footer-rule { position: absolute; left: 150px; top: 179px; width: 900px; height: 1px; background: var(--line); }
  .copyright {
    position: absolute; left: 0; top: 200px; width: 1200px; text-align: center;
    color: var(--white); font-size: 16.5px;
  }
</style>
</head>
<body>
  <div class="top-rule"></div>

  <header class="site-header">
    <div class="brand-name">Hemmingtarn</div>
    <div class="call">
      <svg viewBox="0 0 64 64" aria-hidden="true">
        <path d="M14 6c3-2 6-1 8 2l6 9c1.5 2.5 1 5-1 7l-4 3c2 6 8 13 14 16l3-4c2-2 4.5-2.5 7-1l9 6c3 2 3.5 5 1.5 8l-4 5c-2 2-5 3-8 2C26 52 12 38 7 18c-1-3 0-6 2-8z" fill="#252a36"/>
        <path d="M36 14a14 14 0 0 1 14 14" stroke="#252a36" stroke-width="4" fill="none" stroke-linecap="round"/>
        <path d="M37 4a24 24 0 0 1 23 23" stroke="#252a36" stroke-width="4" fill="none" stroke-linecap="round"/>
      </svg>
      <div>
        <div class="call-label">CALL US:</div>
        <div class="call-number">(555) 014-2368</div>
      </div>
    </div>
  </header>

  <div class="hero-photo" role="img" aria-label="Campers in yellow camp shirts walking through a cornfield with a coach in a pinstripe uniform"></div>
  <div class="title-frame">
    <div class="title-box"><h1>HEMMINGTARN BASEBALL<br>ACADEMY</h1></div>
  </div>

  <p class="intro">This is the place to be if you are looking to give your child a baseball experience second to none! This camp is geared toward baseball players ages 5 to 14 who are looking to improve their skills and knowledge of the game.</p>

  <section class="about">
    <div class="about-photo" role="img" aria-label="Young batter in a red helmet and yellow camp shirt swinging at a practice net"></div>
    <div class="about-card">
      <h2>ABOUT US</h2>
      <p>Local baseball coaching camp for children is in it's 22nd year running a 4-5 week series of summer camps. Each year we use email marketing beginning around December to sell our camps to the parents to sign up their children for one or more weeks. All information about the camps can be seen on our website at <a href="https://hemmingtarn.com/">https://hemmingtarn.com/</a>.</p>
    </div>
  </section>

  <section class="academy">
    <h2>OUR ACADEMY</h2>
    <div class="week w1"><div class="price">$225</div><div class="details"><span class="label">WEEK 1:</span> June 27 - July 1<br>@Oakhollow Park - Fernvale</div></div>
    <div class="week w2"><div class="price">$350</div><div class="details"><span class="label">WEEK 2:</span> July 11 - July 15<br>@Tessler Park-Brookmere</div></div>
    <div class="week w3"><div class="price">$925</div><div class="details"><span class="label">WEEK 3:</span> July 18 - July 22<br>@Oakhollow Road Park -<br>Fernvale</div></div>
    <div class="week w4"><div class="price">$1,125</div><div class="details"><span class="label">WEEK 4:</span> July 25 - July 29<br>@Oakhollow Road Park -<br>Fernvale</div></div>
  </section>

  <div class="objectives-photo" role="img" aria-label="Group photo of campers in yellow shirts on a grass field with trees behind"></div>
  <section class="objectives-card">
    <h2>CAMP OBJECTIVES</h2>
    <p>HEMMINGTARN BASEBALL CAMP provides a safe, fun, and educational environment where both beginner, as well as experienced players can excel. Throughout the week, your child will learn the basic fundamentals of the game and be able to specialize in the position of their choice. Each camper will learn the importance of team work, sportsmanship, and fair play.</p>
  </section>

  <footer class="site-footer">
    <div class="footer-brand">Hemmingtarn</div>
    <div class="contact contact-1">
      <svg viewBox="0 0 24 24" aria-hidden="true"><path d="M5 2c1-.6 2-.3 2.6.6l2 3c.5.8.3 1.7-.3 2.3l-1.3 1c.8 2 2.8 4.2 4.8 5.2l1-1.3c.6-.7 1.5-.8 2.3-.3l3 2c.9.6 1.1 1.7.5 2.6l-1.3 1.6c-.7.8-1.7 1-2.7.7C9 17 4.5 12.5 3 6.5c-.3-1 0-2 .7-2.7z"/></svg>
      <span>(555) 014-2368</span>
      <span class="sep">|</span>
      <svg viewBox="0 0 24 24" aria-hidden="true"><path d="M2 5h20v14H2z M3 6l9 7 9-7" fill="none" stroke="#fff" stroke-width="2"/><path d="M2 5h20L12 12z"/></svg>
      <span>info@hemmingtarn.com</span>
    </div>
    <div class="contact contact-2">
      <svg viewBox="0 0 24 24" aria-hidden="true"><path d="M12 1a7 7 0 0 0-7 7c0 5 7 15 7 15s7-10 7-15a7 7 0 0 0-7-7zm0 10a3 3 0 1 1 0-6 3 3 0 0 1 0 6z"/></svg>
      <span>PO Box 48 Ashdale, New York 10990–4417</span>
    </div>
    <div class="footer-rule"></div>
    <div class="copyright">© 2021 Hemmingtarn. All Rights Reserved</div>
  </footer>
</body>
</html>
```